business card for a massage therapy practice named 'Cedar and Willow Massage Studio'

I really need a trendy, yet easy on the eyes business card to complement my logo. Ideally with some gold or rose gold foil work.

My uploaded file of the logo I have in horizontal but I have a vertical version as well. Another color that is used in the website is a blush pink here and there. I'd like to see some trendy tropical leaves in the design.

```html
<!DOCTYPE html>
<html lang="en">
<head>
<meta charset="utf-8">
<title>Cedar and Willow Massage Studio – Business Card</title>
<link rel="stylesheet" href="https://fonts.googleapis.com/css2?family=EB+Garamond:wght@400;500&family=Dancing+Script:wght@500&display=swap">
<style>
  :root {
    --canvas: #e9e9eb;
    --blush: #f6c3c4;
    --blush-soft: #fbe3e3;
    --paper: #ffffff;
    --leaf-deep: #3f7a55;
    --leaf-mid: #6a9c74;
    --leaf-pale: #a9c8b0;
    --ink: #1d1a1a;
    --wine: #5a2230;
    --rule: #e7a6ac;
    --frame-line: #8f9591;
  }
  * { box-sizing: border-box; margin: 0; padding: 0; }
  html, body { width: 1200px; height: 1200px; overflow: hidden; }
  body {
    background: var(--canvas);
    display: flex;
    flex-direction: column;
    align-items: center;
    justify-content: center;
    gap: 44px;
    font-family: "EB Garamond", Georgia, serif;
  }
  .card {
    position: relative;
    width: 900px;
    height: 514px;
    border-radius: 4px;
    overflow: hidden;
    box-shadow: 0 14px 30px rgba(0,0,0,0.18), 0 2px 6px rgba(0,0,0,0.12);
  }

  /* Front */
  .card-front .foliage {
    position: absolute;
    inset: 0;
    background:
      radial-gradient(ellipse at 8% 20%, var(--leaf-deep) 0%, transparent 38%),
      radial-gradient(ellipse at 92% 85%, var(--leaf-deep) 0%, transparent 40%),
      radial-gradient(ellipse at 85% 15%, var(--leaf-mid) 0%, transparent 35%),
      radial-gradient(ellipse at 15% 90%, var(--leaf-mid) 0%, transparent 38%),
      linear-gradient(135deg, var(--blush) 0%, var(--leaf-pale) 45%, var(--blush) 100%);
  }
  .card-front .name-panel {
    position: absolute;
    left: 92px;
    top: 78px;
    width: 716px;
    height: 358px;
    background: rgba(240, 244, 238, 0.72);
    display: flex;
    align-items: center;
    justify-content: center;
  }
  .card-front .name-panel::after {
    content: "";
    position: absolute;
    inset: 14px;
    border: 1px solid var(--frame-line);
  }
  .studio-name-large {
    font-size: 64px;
    font-weight: 400;
    color: var(--ink);
    text-align: center;
    line-height: 1.1;
  }

  /* Back */
  .card-back {
    background: linear-gradient(100deg, var(--blush) 0%, var(--blush-soft) 22%, var(--paper) 48%, var(--paper) 62%, var(--blush-soft) 82%, var(--blush) 100%);
  }
  .brand {
    position: absolute;
    left: 110px;
    top: 0;
    bottom: 0;
    width: 420px;
    display: flex;
    align-items: center;
    gap: 22px;
  }
  .brand-dot {
    flex: none;
    width: 54px;
    height: 54px;
    border-radius: 50%;
    background: #b59a5e;
  }
  .studio-name {
    font-size: 34px;
    font-weight: 400;
    color: var(--ink);
    line-height: 1.15;
  }
  .divider {
    position: absolute;
    left: 560px;
    top: 150px;
    width: 1px;
    height: 230px;
    background: var(--rule);
  }
  .contact {
    position: absolute;
    left: 590px;
    top: 140px;
    color: var(--wine);
  }
  .person-name {
    font-family: "Dancing Script", cursive;
    font-size: 38px;
    line-height: 1;
  }
  .person-role {
    font-size: 17px;
    margin: 6px 0 20px;
  }
  .contact-list { list-style: none; font-size: 17px; line-height: 1.35; }
  .contact-list li { display: flex; gap: 10px; align-items: flex-start; margin-bottom: 4px; }
  .contact-list li.address { margin-bottom: 18px; }
  .contact-list svg { flex: none; width: 15px; height: 15px; margin-top: 4px; fill: var(--wine); }
</style>
</head>
<body>

<section class="card card-front">
  <div class="foliage" role="img" aria-label="Painted tropical monstera and palm leaves on a blush pink ground"></div>
  <div class="name-panel">
    <p class="studio-name-large">Cedar and Willow</p>
  </div>
</section>

<section class="card card-back">
  <div class="brand">
    <span class="brand-dot"></span>
    <p class="studio-name">Cedar and Willow<br>Massage Studio</p>
  </div>

  <div class="divider"></div>

  <div class="contact">
    <p class="person-name">Mara Ellison</p>
    <p class="person-role">Director</p>
    <ul class="contact-list">
      <li class="address">
        <svg viewBox="0 0 16 16"><path d="M8 0a5.5 5.5 0 0 0-5.5 5.5C2.5 10 8 16 8 16s5.5-6 5.5-10.5A5.5 5.5 0 0 0 8 0zm0 7.8a2.3 2.3 0 1 1 0-4.6 2.3 2.3 0 0 1 0 4.6z"/></svg>
        <span>Dummy city<br>Dummy Country Land</span>
      </li>
      <li>
        <svg viewBox="0 0 16 16"><path d="M3.6 1l2.2 3-1.3 1.6a9 9 0 0 0 5.9 5.9l1.6-1.3 3 2.2-1.2 2.6C7.6 15 1 8.4 1 2.2z"/></svg>
        <span>1-555-014-2290</span>
      </li>
      <li>
        <svg viewBox="0 0 16 16"><path d="M1 3h14v10H1zm1.5 1.2v.3L8 8.6l5.5-4.1v-.3z"/></svg>
        <span>mara@cedarandwillow.com</span>
      </li>
      <li>
        <svg viewBox="0 0 16 16"><path d="M8 1a7 7 0 1 0 0 14A7 7 0 0 0 8 1zm0 1.5c.8 0 1.8 1.8 2 4.5H6c.2-2.7 1.2-4.5 2-4.5zM6 9h4c-.2 2.7-1.2 4.5-2 4.5S6.2 11.7 6 9zM2.6 7a5.5 5.5 0 0 1 2.6-3.9C4.7 4.2 4.5 5.5 4.4 7zm0 2h1.8c.1 1.5.3 2.8.8 3.9A5.5 5.5 0 0 1 2.6 9zm8.2 3.9c.5-1.1.7-2.4.8-3.9h1.8a5.5 5.5 0 0 1-2.6 3.9zM11.6 7c-.1-1.5-.3-2.8-.8-3.9A5.5 5.5 0 0 1 13.4 7z"/></svg>
        <span>www.cedarandwillow.com</span>
      </li>
    </ul>
  </div>
</section>

</body>
</html>
```